Post Card Design - Photo on front, details on back. Logo on both sides.

Back: See the photo of my old card. The back worked well, as it gave me lots of space to write on. The address details are still correct, but the logo has changed to Josephine Sans. Logo can be on one line or on two (if two, align it on the left).
Don't include the 'BEAUTIFUL WEDDING DRESSES...' bit.
I'd like to print this on thicker, slightly coarse paper, so don't go too small on detail.
Here are the Trelo paper details: Paper Stock: Natural Uncoated
Paper Thickness: Premium
Finish: None
Front of Card: I'd like to see options for both pictures:
I think the painted image would look best with a frame in a pale shade and the logo in the frame fairly subtle.
The actual dress photo I'd like to see cropped a bit like in my mock up. You'll need to have a look at how the logo would be best placed on this. You can place it anywhere, or add a banner.
See my website for my brand's look: mirelhoffkin.co.nz
Target Market(s)
Brides
Industry/Entity Type
Wedding Dresses
Contact Information for Business Card
Front: Photo and logo. Back: with details and lots of empty space. See attached photos for loose brief.
Other font styles liked:
- Josephine Sans
Requirements
Must have
- I hand-write the gown designs and price on the back of the card, so there needs to be plenty of empty space.
Nice to have
- As per brief.
Should not have
- It must look clean, romantic, modern. Timeless.

```html
<!DOCTYPE html>
<html lang="en">
<head>
<meta charset="utf-8">
<title>Mirel Hoffkin – Post Card</title>
<link rel="stylesheet" href="https://fonts.googleapis.com/css2?family=Josefin+Sans:wght@300;400&display=swap">
<style>
  :root {
    --backdrop: #e9e9ec;
    --card-cream: #efdcae;
    --card-white: #ffffff;
    --ink: #1c1c1c;
    --bloom-pink: #e9a3a3;
    --bloom-peach: #f2c29a;
    --bloom-ivory: #f4e6cf;
    --edge-gold: #b8902f;
  }
  * { box-sizing: border-box; margin: 0; padding: 0; }
  html, body {
    width: 1200px; height: 1200px; overflow: hidden;
    background: var(--backdrop);
    font-family: "Josefin Sans", sans-serif;
    color: var(--ink);
  }
  .sheet { position: relative; width: 1200px; height: 1200px; }
  .card {
    position: absolute; left: 250px; width: 700px; height: 420px;
    box-shadow: 0 6px 18px rgba(0,0,0,0.12);
    border-bottom: 3px solid var(--edge-gold);
    overflow: hidden;
  }
  /* Front */
  .card-front { top: 150px; background: var(--card-cream); }
  .front-name {
    position: absolute; left: 44px; top: 48px; width: 220px;
    font-weight: 400; font-size: 30px; line-height: 1.3;
    letter-spacing: 2px; text-transform: uppercase;
  }
  .front-artwork {
    position: absolute; left: 280px; top: 30px; width: 380px; height: 360px;
  }
  /* Back */
  .card-back { top: 630px; background: var(--card-white); }
  .back-name {
    position: absolute; left: 44px; top: 48px;
    font-weight: 400; font-size: 30px; letter-spacing: 2px; text-transform: uppercase;
  }
  .contact-list {
    position: absolute; left: 392px; top: 312px; list-style: none;
    font-weight: 300; font-size: 22px; line-height: 30px;
  }
  .contact-list li { display: flex; align-items: center; gap: 8px; }
  .contact-list svg { width: 16px; height: 16px; flex: none; }
</style>
</head>
<body>
<main class="sheet">
  <section class="card card-front">
    <div class="front-name">Mirel<br>Hoffkin</div>
    <svg class="front-artwork" viewBox="0 0 380 360" role="img" aria-label="Watercolour painting of a bridal couple surrounded by pink and peach peonies">
      <defs>
        <radialGradient id="bloom" cx="50%" cy="50%" r="50%">
          <stop offset="0%" stop-color="var(--bloom-ivory)"/>
          <stop offset="45%" stop-color="var(--bloom-pink)"/>
          <stop offset="80%" stop-color="var(--bloom-peach)" stop-opacity="0.7"/>
          <stop offset="100%" stop-color="var(--card-cream)" stop-opacity="0"/>
        </radialGradient>
      </defs>
      <ellipse cx="190" cy="180" rx="190" ry="180" fill="url(#bloom)"/>
    </svg>
  </section>

  <section class="card card-back">
    <div class="back-name">Mirel Hoffkin</div>
    <ul class="contact-list">
      <li>
        <svg viewBox="0 0 16 16" aria-hidden="true"><path d="M4 1.5 6 4.5 4.8 6c.8 1.8 2.3 3.4 4.2 4.3L10.4 9l3 2-1.2 2.8C7 13.5 2.5 9 2 3.2Z" fill="var(--ink)"/></svg>
        +64 9 412 5067
      </li>
      <li>
        <svg viewBox="0 0 16 16" aria-hidden="true" fill="none" stroke="var(--ink)" stroke-width="1.2"><circle cx="8" cy="8" r="6.5"/><ellipse cx="8" cy="8" rx="3" ry="6.5"/><path d="M1.5 8h13M2.6 4.5h10.8M2.6 11.5h10.8"/></svg>
        mirelhoffkin.co.nz
      </li>
      <li>
        <svg viewBox="0 0 16 16" aria-hidden="true" fill="none" stroke="var(--ink)" stroke-width="1.2"><rect x="1.5" y="3.5" width="13" height="9"/><path d="M1.5 3.5 8 9l6.5-5.5M1.5 12.5l5-4.5M14.5 12.5l-5-4.5"/></svg>
        mira@mirelhoffkin.co.nz
      </li>
    </ul>
  </section>
</main>
</body>
</html>
```